Blow Dry Bar Business Cards

These cards must be eye catching and modern.
You must be willing to work fast and make changes.

Winner will be offered other projects

Files 1 THIS IS THE STYLE CARDS I AM INTRESTED IN!!!
Please be creative, I am paying for my own eye catching design. I need files to be nexa press ready.

COLORS THAT ARE PAINTED INSIDE MY SHOP:
- - - http://www.quorvelpaint.example/en/explore-colors/painter/color-selector.html?colors=4007-3C

- - - http://www.brandivex.example/color/paint-colors/hidden-corridor-d58-2

I want the business cards sleek and modern if you use the logo please correct imperfections. I added the part that says Blow Dry Bar (see website).
Do not be afraid to separate the blow dryer from the name to make the cards look like the file with the pink elephant.

SHOULD INCLUDE
*Blow Dryer (we are a blow dry bar not a salon we do not cut or color so do not include sheers of any kind)
*BUSINESS NAME: Simply Swept Upward - Blow Dry Bar (PLEASE SEE MY WEBSITE)
* Website: SIMPLYSWEPTUPWARD.EXAMPLE
*Phone number (555) 014-2763
Updates

Nexa press said it can be submitted in JPG

http://www.brandivex.example/color/paint-colors/hidden-corridor-d58-2 http://www.quorvelpaint.example/en/explore-colors/painter/color-selector.html?colors=4007-3C ^^^^ These links will take you to the color paint that is painted inside my shop.

Target Market(s)

AGES 18 - 55 WOMEN
HIGH END MARKET

Industry/Entity Type

Salon

Requirements
Must have
• SEE COLOR EXAMPLE FILE
BLOW DRYER
UNIQUE
I LIKE THE CARD WITH THE PINK ELEPHANT THE BEST
Nice to have
• BE AS CREATIVE AND MODERN AS POSSIBLE DO NOT COPY ANY OF THE CARDS BELOW.
Should not have
• SCISSORS
PINK

```html
<!DOCTYPE html>
<html lang="en">
<head>
<meta charset="utf-8">
<title>Swept Upward — Business Cards</title>
<link rel="stylesheet" href="https://fonts.googleapis.com/css2?family=Arvo&family=Cinzel:wght@400&display=swap">
<style>
  :root {
    --bg: #2b2d31;
    --card-top: #3a1a14;
    --card-bottom: #1c0c09;
    --gold: #e9df17;
    --white: #f4f1ea;
  }
  * { box-sizing: border-box; margin: 0; padding: 0; }
  html, body { width: 1200px; height: 960px; overflow: hidden; }
  body {
    background: var(--bg);
    position: relative;
  }
  .card {
    position: absolute;
    top: 130px;
    width: 400px;
    height: 700px;
    border-radius: 28px;
    background: linear-gradient(160deg, var(--card-top), var(--card-bottom));
    overflow: hidden;
  }
  .card--front { left: 170px; }
  .card--back { left: 630px; }

  .vertical-name {
    position: absolute;
    top: 60px;
    right: 70px;
    display: flex;
    flex-direction: column;
    align-items: center;
    font-family: "Arvo", serif;
    color: var(--white);
    font-size: 20px;
    line-height: 30px;
  }
  .vertical-name .gap { height: 30px; }

  .brand {
    position: absolute;
    display: flex;
    align-items: center;
    gap: 12px;
    font-family: "Arvo", serif;
    color: var(--gold);
    font-size: 44px;
    white-space: nowrap;
  }
  .brand-dot {
    width: 24px; height: 24px;
    border-radius: 50%;
    background: var(--gold);
    flex: none;
  }
  .card--front .brand { left: 40px; bottom: 110px; }
  .card--back .brand { left: 40px; top: 100px; }

  .contact {
    position: absolute;
    left: 34px;
    right: 30px;
    bottom: 110px;
    list-style: none;
    font-family: "Cinzel", serif;
    color: var(--gold);
    font-size: 15px;
  }
  .contact li {
    display: flex;
    justify-content: space-between;
    align-items: center;
    gap: 12px;
    margin-top: 10px;
  }
  .contact .lines { display: flex; flex-direction: column; line-height: 20px; }
  .contact svg { width: 18px; height: 18px; flex: none; fill: var(--white); }
</style>
</head>
<body>
  <section class="card card--front">
    <div class="vertical-name" aria-label="Swept Upward">
      <span>S</span><span>w</span><span>e</span><span>p</span><span>t</span>
      <span class="gap"></span>
      <span>U</span><span>p</span><span>w</span><span>a</span><span>r</span><span>d</span>
    </div>
    <div class="brand"><span>Swept Upward</span><span class="brand-dot"></span></div>
  </section>

  <section class="card card--back">
    <div class="brand"><span>Swept Upward</span><span class="brand-dot"></span></div>
    <ul class="contact">
      <li>
        <span class="lines"><span>(555) 014-2763</span></span>
        <svg viewBox="0 0 24 24" aria-label="Phone"><path d="M6.6 10.8a15 15 0 0 0 6.6 6.6l2.2-2.2c.3-.3.7-.4 1-.2 1.1.4 2.3.6 3.6.6.6 0 1 .4 1 1V20c0 .6-.4 1-1 1A17 17 0 0 1 3 4c0-.6.4-1 1-1h3.5c.6 0 1 .4 1 1 0 1.3.2 2.5.6 3.6.1.3 0 .7-.2 1z"/></svg>
      </li>
      <li>
        <span class="lines"><span>www.simplysweptupward.example</span></span>
        <svg viewBox="0 0 24 24" aria-label="Website"><path d="M12 2a10 10 0 1 0 0 20 10 10 0 0 0 0-20zm0 2c1 1.3 1.8 3.4 2 6h-4c.2-2.6 1-4.7 2-6zM4.1 11h3.9c.1 2.3.7 4.4 1.6 6A8 8 0 0 1 4.1 11zm0-2A8 8 0 0 1 9.6 4c-.9 1.6-1.5 3.7-1.6 5zm5.9 2h4c-.2 2.6-1 4.7-2 6-1-1.3-1.8-3.4-2-6zm4.4 6c.9-1.6 1.5-3.7 1.6-6h3.9a8 8 0 0 1-5.5 6zM16 9c-.1-1.3-.7-3.4-1.6-5a8 8 0 0 1 5.5 5z"/></svg>
      </li>
      <li>
        <span class="lines"><span>info@simplysweptupward.example</span></span>
        <svg viewBox="0 0 24 24" aria-label="Email"><path d="M3 5h18v14H3zm2 2v.4l7 5 7-5V7zm0 2.9V17h14V9.9l-7 5z"/></svg>
      </li>
      <li>
        <span class="lines"><span>418 Heron Bend Drive Suite 12</span><span>Maple Hollow, Texas 75099</span></span>
        <svg viewBox="0 0 24 24" aria-label="Address"><path d="M12 2a7 7 0 0 0-7 7c0 5 7 13 7 13s7-8 7-13a7 7 0 0 0-7-7zm0 9.5A2.5 2.5 0 1 1 12 6.5a2.5 2.5 0 0 1 0 5z"/></svg>
      </li>
    </ul>
  </section>
</body>
</html>
```